Meadow Paw Web Site

We have basically a start up business that I need help with. This project is just for the web site.

Our product is a frozen raw pet food that promotes weight control, less shedding, smaller stools and an overall better health. The product is in nugget form similar to what you would see in a steak shish kabob. I only share that with you in case you want to incorporate that in the design.

We have been in business for 17 years but all of our sales have been word of mouth. We are going to be launching an infomercial this summer and I need everything stated previously to be completed before we can launch the infomercial.

We need the following (6) pages:

Home:
This is where we need to have the ability to purchase our products. Our main goal is to get the consumer to purchase our product. We have our own shopping cart so we just need to allow for the insertion of that shopping cart.

Why Raw:
This will just be a page with 4-5 paragraphs and an embedded YouTube video.

How to Use:
We will need a page with a chart (4 Columns wide with 6 rows) as well as an embedded YouTube video.

Customer Success Stories:
Allow us to add these as we move forward. I need a placeholder for an image of the customers pet and a paragraph or two explaining the situation

Where to Buy:
- Online - Find a Retailer - Find a Local Distributor - Call to Order

Contact Us:
Copper Ridge Holdings, Inc.
2740 Copper Rd
Eagan, MN 55148
(800) xxx-xxxx

We need to provide links to our to be created... Facebook page, Twitter Account, Youtube Channel, Google circle, Blog
Updates

All, I have received many front page designs that look good.  Please notice in the brief that I need multiple pages built not just the home page.  

Thanks,

Dale

Reason: I need to see the rest of the pages. Thanks, Dale

Target Market(s)

Women between the ages of 30 & 60.

Industry/Entity Type

Shopping

```html
<!DOCTYPE html>
<html lang="en">
<head>
<meta charset="utf-8">
<title>Meadow Paw – Home</title>
<link href="https://fonts.googleapis.com/css2?family=Open+Sans:wght@400;600;700;800&display=swap" rel="stylesheet">
<style>
:root{
  --orange:#f47b12;
  --orange-dark:#e0600a;
  --red:#d8432b;
  --ink:#2b2b2b;
  --muted:#777;
  --black:#151515;
  --rule:#e2e2e2;
  --foot:#f2f2f2;
  --yellow:#ffcc1f;
  --brown:#3a2410;
}
*{box-sizing:border-box;margin:0;padding:0}
html,body{width:688px;height:1200px;overflow:hidden;background:#fff}
body{font-family:'Open Sans',Arial,sans-serif;color:var(--ink);font-size:7px;line-height:1.45;position:relative}
.wrap{position:absolute;left:98px;width:492px}

/* top bar */
.topbar{position:absolute;top:0;left:0;width:688px;height:18px;background:var(--black)}
.topbar .links{left:98px;top:4px;position:absolute;color:#ddd;font-size:6px;display:flex;gap:12px}
.topbar .links span::before{content:"";display:inline-block;width:5px;height:5px;background:#bbb;border-radius:1px;margin-right:3px;vertical-align:-0.5px}
.social{position:absolute;right:98px;top:4px;display:flex;gap:3px}
.social i{display:block;width:10px;height:10px;border-radius:50%;background:#4a6fb0}
.social i:nth-child(2){background:#3fa8e0}
.social i:nth-child(3){background:#d23b2a}
.social i:nth-child(4){background:#d86a1e}
.social i:nth-child(5){background:#e8871c}

/* header */
.header{position:absolute;top:18px;left:0;width:688px;height:310px;background:linear-gradient(180deg,#f7941d 0%,var(--orange) 40%,var(--orange-dark) 100%)}
.logo{position:absolute;left:103px;top:6px;display:flex;align-items:center;gap:6px;background:var(--brown);padding:9px 10px;border-radius:3px}
.logo i{width:14px;height:14px;background:var(--yellow)}
.logo b{font-size:12px;font-weight:800;color:#fff;letter-spacing:.2px}
.phone{position:absolute;right:98px;top:36px;color:#fff;font-size:13px;font-weight:700;display:flex;align-items:center;gap:5px}
.cart{position:absolute;left:332px;top:70px;width:106px;height:26px;background:var(--yellow);border-radius:2px;display:flex;align-items:center;padding-left:7px;gap:5px;font-size:6.5px;font-weight:700;color:var(--brown)}
.nav{position:absolute;top:119px;left:98px;width:492px;height:21px;background:#fff;display:flex;font-size:6.5px;font-weight:600}
.nav a{padding:0 13px;line-height:21px;color:var(--ink);text-decoration:none}
.nav a.active{background:var(--orange);color:#fff}

/* hero */
.hero{position:absolute;top:140px;left:98px;width:492px;height:208px;background:linear-gradient(180deg,#fff,#f3f3f3);box-shadow:0 2px 6px rgba(0,0,0,.2)}
.hero h1{position:absolute;left:16px;top:20px;font-size:20px;font-weight:800;color:var(--orange)}
.hero p{position:absolute;left:16px;top:54px;width:205px;font-size:6px;color:#555}
.hero .deal{position:absolute;left:16px;top:138px;font-size:15px;font-weight:700;color:var(--orange)}
.btn{display:inline-block;background:var(--red);color:#fff;font-weight:700;font-size:6px;padding:4px 8px;border-radius:2px}
.hero .btn{position:absolute;left:16px;top:168px}
.dots{position:absolute;left:68px;top:171px;display:flex;gap:4px}
.dots i{width:5px;height:5px;border-radius:50%;background:#555}
.hero-art{position:absolute;right:14px;top:8px;width:220px;height:192px;background:radial-gradient(circle at 45% 50%,#e6b365 0%,#c58a3c 45%,#f3f3f3 75%)}

/* section titles */
.sec-title{font-size:11px;font-weight:600;color:var(--ink)}
.sec-title em{font-style:normal;color:var(--orange)}
.rule{height:1px;background:var(--rule);margin-top:5px}

/* featured */
.featured{top:458px}
.arrows{position:absolute;right:0;top:0;display:flex;gap:3px}
.arrows span{width:12px;height:12px;border-radius:50%;background:var(--red);display:flex;align-items:center;justify-content:center}
.products{display:flex;gap:14px;margin-top:14px}
.card{width:112px;border:1px solid var(--rule);padding:5px;background:#fff}
.card .pic{height:76px;background:linear-gradient(180deg,#efe7dc,#cdb79a)}
.card:nth-child(2) .pic{background:linear-gradient(180deg,#f1eadf,#b89270)}
.card:nth-child(3) .pic{background:linear-gradient(180deg,#e9e2d3,#8f7a4e)}
.card:nth-child(4) .pic{background:linear-gradient(180deg,#eef0e6,#9fae7a)}
.card h3{font-size:6.5px;font-weight:600;margin-top:7px}
.card p{font-size:5.3px;color:var(--muted);margin-top:2px;line-height:1.35}
.card .price{font-size:7.5px;font-weight:700;margin-top:4px}
.card .btn{margin-top:4px;font-size:5.3px;padding:3px 6px}

/* stories + recipes */
.stories{top:666px;width:236px}
.recipes{top:666px;left:354px;width:236px}
.story-pic{margin-top:12px;height:150px;background:radial-gradient(circle at 50% 50%,#c79a55,#8a5a25 70%,#6b431b)}
.stories h3{font-size:7.5px;font-weight:600;margin-top:10px}
.stories p{font-size:5.6px;color:#555;margin-top:6px}
.stories .btn{margin-top:12px;background:var(--orange);font-size:6px;padding:5px 9px}
.recipe{display:flex;gap:8px;margin-top:12px;height:78px}
.recipe .thumb{width:58px;height:58px;flex:none;background:linear-gradient(135deg,#d8c29a,#8c6a3a)}
.recipe:nth-child(4) .thumb{background:linear-gradient(135deg,#c9b48c,#6d5a3a)}
.recipe h4{font-size:6.3px;font-weight:600}
.recipe .price{font-size:7.5px;font-weight:700;margin-top:3px}
.recipe p{font-size:5.3px;color:var(--muted);margin-top:2px;line-height:1.35}
.recipe .more{display:block;text-align:right;color:var(--orange);font-size:5.3px;font-weight:600;margin-top:4px}

/* signup band */
.band{position:absolute;top:984px;left:0;width:688px;height:72px;background:var(--orange)}
.signup{position:absolute;left:100px;top:26px;display:flex;align-items:center;gap:8px;color:#fff;font-size:10px;font-weight:600}
.signup .field{width:78px;height:14px;background:#fff;border-radius:2px;margin-left:10px}
.signup .go{width:16px;height:16px;border-radius:50%;background:var(--black);display:flex;align-items:center;justify-content:center;margin-left:-10px}
.ship{position:absolute;left:378px;top:14px;color:#fff;display:flex;gap:8px}
.ship h5{font-size:9px;font-weight:600}
.ship p{font-size:5.3px;width:170px;line-height:1.4;margin-top:2px}

/* footer */
.footer{position:absolute;top:1056px;left:0;width:688px;height:112px;background:var(--foot)}
.cols{position:absolute;left:98px;top:14px;display:flex}
.col{width:128px}
.col:nth-child(2){width:112px}
.col:nth-child(3){width:112px}
.col h6{font-size:7px;font-weight:600;margin-bottom:6px}
.col li{list-style:none;font-size:5.5px;color:#555;line-height:1.8}
.cards{display:flex;flex-wrap:wrap;gap:4px;width:90px}
.cards i{width:24px;height:14px;border-radius:2px;background:#d6d6d6}
.cards i:nth-child(1){background:#2f5fa8}
.cards i:nth-child(2){background:#e39a2a}
.cards i:nth-child(3){background:#4b8fd1}
.cards i:nth-child(4){background:#1b3e80}
.cards i:nth-child(5){background:#c0392b}
.addr li{display:flex;gap:4px;align-items:flex-start}
.addr li::before{content:"";flex:none;width:5px;height:5px;border-radius:50%;background:var(--orange);margin-top:3px}
.bottombar{position:absolute;top:1168px;left:0;width:688px;height:32px;background:var(--black);color:#aaa;font-size:5.5px}
.bottombar span{position:absolute;left:98px;top:12px}
</style>
</head>
<body>

<div class="topbar">
  <div class="links"><span>Register</span><span>My Account</span><span>Login</span></div>
  <div class="social"><i></i><i></i><i></i><i></i><i></i></div>
</div>

<header class="header">
  <div class="logo"><i></i><b>Meadow Paw</b></div>
  <div class="phone">
    <svg width="11" height="11" viewBox="0 0 24 24"><path fill="#fff" d="M6.6 10.8a15 15 0 006.6 6.6l2.2-2.2c.3-.3.7-.4 1-.2 1.1.4 2.3.6 3.6.6.6 0 1 .4 1 1V20c0 .6-.4 1-1 1A17 17 0 013 4c0-.6.4-1 1-1h3.5c.6 0 1 .4 1 1 0 1.3.2 2.5.6 3.6.1.3 0 .7-.2 1z"/></svg>
    888-555-0142
  </div>
  <div class="cart">
    <svg width="11" height="10" viewBox="0 0 24 22"><path d="M1 2h4l3 12h12l3-9H7" fill="none" stroke="#3a2410" stroke-width="2.4"/><circle cx="9" cy="19" r="2" fill="#3a2410"/><circle cx="19" cy="19" r="2" fill="#3a2410"/></svg>
    Your cart (0 items)
  </div>
</header>

<nav class="nav">
  <a class="active">Home</a><a>Why Raw</a><a>How to Use</a><a>Success Stories</a><a>Where to Buy</a><a>Contact</a>
</nav>

<section class="hero">
  <h1>Dog RAW Food</h1>
  <p>Frozen raw nuggets made from simple whole ingredients help your dog keep a healthy weight, shed less and feel better every day. Serve straight from the freezer after thawing and watch mealtime become the best part of the day for your pet.</p>
  <div class="deal">40 % OFF</div>
  <span class="btn">SHOP NOW</span>
  <div class="dots"><i></i><i></i><i></i><i></i></div>
  <div class="hero-art" role="img" aria-label="Happy dog beside a bag of raw pet food"></div>
</section>

<section class="wrap featured">
  <h2 class="sec-title">Featured Products</h2>
  <div class="arrows">
    <span><svg width="6" height="6" viewBox="0 0 10 10"><path d="M7 1L3 5l4 4" stroke="#fff" stroke-width="2" fill="none"/></svg></span>
    <span><svg width="6" height="6" viewBox="0 0 10 10"><path d="M3 1l4 4-4 4" stroke="#fff" stroke-width="2" fill="none"/></svg></span>
  </div>
  <div class="rule"></div>
  <div class="products">
    <article class="card"><div class="pic" role="img" aria-label="Bag of raw dog food"></div><h3>Eget elementum vel</h3><p>Fresh raw nuggets for active dogs of every size.</p><div class="price">$299.99</div><span class="btn">Add To Cart</span></article>
    <article class="card"><div class="pic" role="img" aria-label="Natural chew treats"></div><h3>Excepteur sint occaecat</h3><p>Slow dried chews that keep teeth clean and strong.</p><div class="price">$299.99</div><span class="btn">Add To Cart</span></article>
    <article class="card"><div class="pic" role="img" aria-label="Bag of grain free pet food"></div><h3>Anim magna ipsum dolor</h3><p>Grain free blend with lean meat and garden greens.</p><div class="price">$299.99</div><span class="btn">Add To Cart</span></article>
    <article class="card"><div class="pic" role="img" aria-label="Bag of dry cat food"></div><h3>Ipsum dolor sit amet</h3><p>Light formula that helps older pets stay trim.</p><div class="price">$299.99</div><span class="btn">Add To Cart</span></article>
  </div>
</section>

<section class="wrap stories">
  <h2 class="sec-title">Success <em>Stories</em></h2>
  <div class="rule"></div>
  <div class="story-pic" role="img" aria-label="Close view of raw pet food nuggets"></div>
  <h3>Brookflow Deluxe Pet Fountain for Cats</h3>
  <p>Our cat Bella had never cared much for her water bowl, and we worried she was not drinking enough. After a few weeks with the fountain and a switch to raw nuggets she drinks often, her coat is soft and she is full of energy again.</p>
  <p>Pet owners tell us the same story every week. Small daily changes to food and water add up, and a happy pet is the best proof that simple fresh feeding works.</p>
  <span class="btn">Learn More</span>
</section>

<section class="wrap recipes">
  <h2 class="sec-title">Recipes And <em>Good Food</em></h2>
  <div class="rule"></div>
  <div class="recipe"><div class="thumb" role="img" aria-label="Pet food recipe dish"></div><div><h4>Meet the Animal in the shadows</h4><div class="price">$90.00</div><p>A hearty frozen mix of lean beef and vegetables that shy eaters love. Thaw overnight and serve at room temperature for best results.</p><span class="more">Read More</span></div></div>
  <div class="recipe"><div class="thumb" role="img" aria-label="Bowl of raw pet food"></div><div><h4>Drugs that Deaden Your Body of Magnesium</h4><div class="price">$90.00</div><p>Learn which minerals matter most for your pet and how a balanced raw diet keeps bones, joints and muscles strong for years.</p><span class="more">Read More</span></div></div>
  <div class="recipe"><div class="thumb" role="img" aria-label="Fresh ingredients for pet meals"></div><div><h4>Barking For Good Wellness Factor</h4><div class="price">$90.00</div><p>Simple meal ideas that support weight control and a shiny coat, with portion tips for small, medium and large dogs.</p><span class="more">Read More</span></div></div>
</section>

<section class="band">
  <div class="signup">
    <svg width="20" height="14" viewBox="0 0 20 14"><rect x="1" y="1" width="18" height="12" rx="1" fill="none" stroke="#fff" stroke-width="1.6"/><path d="M1 1l9 7 9-7" fill="none" stroke="#fff" stroke-width="1.6"/></svg>
    Sign up
    <span class="field"></span>
    <span class="go"><svg width="7" height="7" viewBox="0 0 10 10"><path d="M1 5h7M5 2l3 3-3 3" stroke="#fff" stroke-width="1.6" fill="none"/></svg></span>
  </div>
  <div class="ship">
    <svg width="26" height="18" viewBox="0 0 26 18"><rect x="1" y="2" width="15" height="11" fill="none" stroke="#fff" stroke-width="1.6"/><path d="M16 6h5l4 4v3h-9z" fill="none" stroke="#fff" stroke-width="1.6"/><circle cx="6" cy="15" r="2" fill="#fff"/><circle cx="20" cy="15" r="2" fill="#fff"/></svg>
    <div><h5>Free Shipping</h5><p>Free delivery on every order over $75 shipped within the lower states, packed frozen in insulated boxes straight to your door.</p></div>
  </div>
</section>

<footer class="footer">
  <div class="cols">
    <div class="col"><h6>Information</h6><ul><li>About Us</li><li>Terms and conditions of use</li><li>Returns</li><li>Sitemap</li></ul></div>
    <div class="col"><h6>Services</h6><ul><li>Online Shopping</li><li>Orders and Returns</li><li>Discount offer</li><li>FAQ</li></ul></div>
    <div class="col"><h6>Make a Payment</h6><div class="cards"><i></i><i></i><i></i><i></i><i></i><i></i></div></div>
    <div class="col addr"><h6>Address</h6><ul><li>2740 Copper Rd, Eagan, MN 55148</li><li>Call us: 888-555-0142</li><li>info@meadowpaw.com</li></ul></div>
  </div>
</footer>

<div class="bottombar"><span>© 2014 Meadow Paw. All rights reserved</span></div>

</body>
</html>
```